KRL Stationery Design Project

Dear Designers,
We need a new stationery design for company to match our new logo.
Designers should provide a design for the following:
1. Business Card: 3.5x2 Inches.
2. Letterhead: A4 size.
3. Envelops: 25x35.5 Cm.
You can keep the Arabic name at the bottom of the logo Or you can use the separate attached Arabic Name.
Please refer to the attached logo guide for design information.
Sample Business Card information:
Name: Tarek Sowan
Position: Operation Manager
Tel: +966 920007164 Ex. 500
Fax: +966 (3)8842617
Mob: +966 (5)00263817
email: tarek@krl-example.com.sa
URL: www.krl-example.com.sa
Address:
Nakheel Heights, Suite 718
Zayed bin Omar Str.
Khobar, 31847
Saudi Arabia
Updates
Dear All,
Please note, we had uploaded our logo along with Arabic writing in Adobe illustrator format (.ai).
Regards,
Karim
Dear All,
A sample data for the business card had been added as per your request.
Regards,
Karim

```html
<!DOCTYPE html>
<html lang="en">
<head>
<meta charset="utf-8">
<title>KRL Business Card</title>
<link rel="stylesheet" href="https://fonts.googleapis.com/css2?family=Open+Sans:ital,wght@0,400;0,700;1,700&display=swap">
<style>
  :root {
    --backdrop: #2b2b2b;
    --card: #ffffff;
    --navy: #0c2d4e;
    --grey: #9c9c9c;
    --ink: #333333;
  }
  * { margin: 0; padding: 0; box-sizing: border-box; }
  html, body { width: 960px; height: 1200px; overflow: hidden; }
  body {
    background: var(--backdrop);
    font-family: "Open Sans", Arial, sans-serif;
    position: relative;
  }
  .card {
    position: absolute;
    width: 840px;
    height: 480px;
    background: var(--card);
    border-radius: 30px;
    overflow: hidden;
  }
  .card-front { left: 53px; top: 83px; }
  .card-back { left: 57px; top: 625px; }
  .swoosh { position: absolute; inset: 0; width: 840px; height: 480px; }
  .brand {
    position: absolute;
    display: flex;
    align-items: center;
    color: var(--navy);
    font-weight: 700;
    letter-spacing: 2px;
  }
  .brand-mark {
    display: inline-block;
    background: var(--navy);
    border-radius: 50%;
  }
  .card-front .brand { left: 40px; top: 70px; font-size: 96px; gap: 22px; }
  .card-front .brand-mark { width: 40px; height: 40px; }
  .card-back .brand {
    left: 0; right: 0; top: 150px;
    justify-content: center;
    font-size: 150px; gap: 34px;
  }
  .card-back .brand-mark { width: 60px; height: 60px; }
  .contact { position: absolute; left: 39px; top: 232px; color: var(--ink); }
  .person { color: var(--navy); font-size: 26px; line-height: 36px; margin-bottom: 8px; }
  .person .role { font-size: 20px; }
  .line { font-size: 20px; line-height: 35px; }
  .line b { font-style: italic; font-weight: 700; }
  .address { font-size: 20px; line-height: 28px; margin-top: 12px; }
</style>
</head>
<body>
  <section class="card card-front">
    <svg class="swoosh" viewBox="0 0 840 480" aria-hidden="true">
      <path fill="var(--navy)" d="M668,0 H840 V480 H470 C660,430 792,330 792,190 C792,110 740,50 668,0Z"/>
      <path fill="var(--card)" d="M462,480 C650,432 780,330 782,180 C790,330 680,440 560,480Z"/>
      <path fill="var(--grey)" d="M450,480 C640,430 770,330 775,185 C780,310 690,430 545,480Z"/>
    </svg>
    <div class="brand"><span class="brand-mark"></span>KRL</div>
    <div class="contact">
      <p class="person">Your Name - <span class="role">Designation</span></p>
      <p class="line"><b>t</b> : 123-123-1234 &nbsp;|&nbsp; <b>f</b> : 123-123-1234</p>
      <p class="line"><b>e</b> : info@krl-example.com.sa</p>
      <p class="line"><b>w</b> : www.krl-example.com.sa</p>
      <p class="address">1234, Suite# 123<br>Street Name, Country Code</p>
    </div>
  </section>

  <section class="card card-back">
    <div class="brand"><span class="brand-mark"></span>KRL</div>
  </section>
</body>
</html>
```